Tampa Bay fishing guide needs stunning website.

I currently have a site - www.reelcoveguide.net which I personally put together using the Pagely platform and I am looking for a redesign on a different platform (Sitecraft?) that will allow me to easily create landing pages in the future. Would like to have a block for visitors to opt in to newsletter. Need social media links on all pages.

I would like to let my visitors know that I am able to handle their fishing charter needs here in the Tampa Bay area, if I'm not available for the dates they are looking to go I can refer them to a reputable captain in the area.

Target Market(s)

United States

Industry/Entity Type

Tourism

Coding

Coded - Design and coding required

Number of Pages Required

5+ page

Font styles to use
Sans Serif

Colors
0355a3
3176b5
85abd2
fbf289

Requirements
Must have
• Mobile Responsive, Ability to insert Vantor Metrics, Chatterbox pixels, ability to add custom landing pages in future
Nice to have
• Clean, easy navigation

```html
<!DOCTYPE html>
<html lang="en">
<head>
<meta charset="utf-8">
<title>Capt. Wade Harlan – Tampa Bay Fishing Guide</title>
<link href="https://fonts.googleapis.com/css2?family=Open+Sans:wght@400;600;700&family=Roboto+Condensed:wght@400;700&display=swap" rel="stylesheet">
<style>
:root{
  --blue:#0355a3;
  --blue-mid:#3176b5;
  --blue-light:#85abd2;
  --yellow:#fbf289;
  --ink:#1d1d1d;
  --body:#555;
  --line:#c9c9c9;
  --white:#fff;
}
*{box-sizing:border-box;margin:0;padding:0}
html,body{width:1200px;height:2936px;overflow:hidden;background:var(--white)}
body{font-family:"Open Sans",sans-serif;color:var(--body);position:relative}
.abs{position:absolute}
.cond{font-family:"Roboto Condensed",sans-serif}

/* header */
.site-header{position:absolute;top:0;left:0;width:1200px;height:125px;background:var(--white)}
.brand{position:absolute;left:78px;top:34px;display:flex;align-items:center;gap:14px}
.brand-dot{width:22px;height:22px;border-radius:50%;background:var(--blue-mid)}
.brand-name{font-family:"Roboto Condensed",sans-serif;font-weight:700;font-size:40px;color:var(--blue)}
.top-mail{position:absolute;left:568px;top:10px;font-size:16px;color:#555;display:flex;align-items:center;gap:12px}
.top-phone{position:absolute;left:802px;top:0;width:163px;height:41px;background:var(--blue);color:var(--white);font-weight:600;font-size:17px;display:flex;align-items:center;justify-content:center;gap:10px;border-radius:0 0 3px 3px}
.top-social{position:absolute;left:1024px;top:11px;display:flex;gap:20px}
.top-social span{width:18px;height:18px;border-radius:3px;background:var(--blue-mid)}
.main-nav{position:absolute;right:77px;top:70px;display:flex;gap:30px;font-size:17.5px;color:var(--blue)}
.main-nav a{color:var(--blue);text-decoration:none}
.main-nav a.active{border-bottom:2px solid var(--blue);padding-bottom:4px}

/* hero */
.hero{position:absolute;top:125px;left:0;width:1200px;height:650px;background:linear-gradient(120deg,#14664f 0%,#1f7f6a 30%,#5f8f86 50%,#b9c4c8 68%,#7a93ab 85%,#5a7390 100%)}
.hero-title{position:absolute;left:78px;top:120px;background:rgba(0,0,0,.45);padding:8px 14px 12px}
.hero-title h1{font-family:"Roboto Condensed",sans-serif;font-weight:700;font-size:54px;color:var(--white);line-height:1.1;letter-spacing:.5px}
.hero-title p{font-size:23px;color:var(--white);line-height:1.35;margin-top:8px}
.btn-yellow{position:absolute;left:78px;top:298px;width:196px;height:50px;background:var(--yellow);color:var(--blue);font-weight:700;font-size:17px;display:flex;align-items:center;justify-content:center}

/* welcome */
.contact-card{position:absolute;left:78px;top:728px;width:270px;height:378px;background:var(--blue);padding:0 10px 10px}
.contact-card h3{font-family:"Roboto Condensed",sans-serif;font-weight:400;color:var(--white);font-size:23px;text-align:center;height:54px;line-height:54px}
.contact-card .inner{background:var(--white);height:304px;padding:14px 12px}
.field{border:1px solid var(--line);height:42px;padding:0 10px;font-size:14px;color:#999;display:flex;align-items:center;margin-bottom:10px}
.field.tall{height:62px;align-items:flex-start;padding-top:10px}
.btn-blue{background:var(--blue-mid);color:var(--white);font-size:16px;display:flex;align-items:center;justify-content:center}
.contact-card .btn-blue{width:106px;height:46px;margin:10px auto 0}
.welcome h2{position:absolute;left:415px;top:822px;font-family:"Roboto Condensed",sans-serif;font-weight:400;font-size:46px;color:var(--ink)}
.welcome h2 em,.section-title em{font-style:normal;color:var(--blue)}
.welcome p{position:absolute;left:413px;top:892px;width:715px;font-size:15px;line-height:24px;color:#666}
.btn-solid{background:var(--blue);color:var(--white);display:flex;align-items:center;justify-content:center;font-size:18px;gap:10px}
.welcome .btn-solid{position:absolute;left:411px;top:1050px;width:166px;height:52px}

/* pickup */
.pickup{position:absolute;top:1160px;left:0;width:1200px;height:594px;background:linear-gradient(180deg,#e7e48a 0%,#d8da7a 50%,#c9cd6e 100%)}
.section-title{font-family:"Roboto Condensed",sans-serif;font-weight:400;font-size:46px;color:var(--ink);text-align:center;position:absolute;left:0;width:1200px}
.pickup .sub{position:absolute;left:0;width:1200px;text-align:center;font-size:17px;color:var(--ink)}
.loc{position:absolute;top:190px;width:322px}
.loc .map{height:196px;background:linear-gradient(135deg,#a9d3ef 0%,#cfe4c9 45%,#eae6dc 100%)}
.loc .label{height:54px;background:var(--blue);color:var(--white);font-family:"Roboto Condensed",sans-serif;font-size:23px;text-align:center;line-height:54px}
.view-all{position:absolute;left:522px;width:155px;height:58px;font-size:19px}

/* rates */
.rate-img{position:absolute;height:138px;width:208px;background:linear-gradient(135deg,#6f8a6a 0%,#a9b8a9 50%,#e8ece8 100%)}
.rate-img.b{background:linear-gradient(135deg,#4d6f8e 0%,#8ca7bf 55%,#c9d4de 100%)}
.rate-text{position:absolute;width:260px;font-size:15px;line-height:24px;color:#666}
.rate-text .name{color:var(--blue);font-size:15.5px}
.rate-text .price{color:var(--ink);font-size:15px;margin-bottom:10px}
.rate-text a{color:var(--blue);text-decoration:underline}

/* gift */
.gift-photo{position:absolute;left:714px;top:2163px;width:486px;height:479px;background:linear-gradient(90deg,rgba(255,255,255,1) 0%,#b8cfe0 25%,#6f93b3 60%,#55789a 100%)}
.gift-sub{position:absolute;left:78px;width:636px;text-align:center;font-size:16px;color:#444}
.gift-field{position:absolute;border:1px solid var(--line);font-size:15px;color:#666;padding:0 10px;display:flex;align-items:center}
.gift-note{position:absolute;left:546px;top:2462px;width:170px;font-size:15px;line-height:22px;color:#666}
.gift-submit{position:absolute;left:399px;top:2538px;width:310px;height:50px;font-weight:700;font-size:19px}

/* footer */
.site-footer{position:absolute;top:2642px;left:0;width:1200px;height:239px;background:var(--yellow);border-top:3px solid var(--blue)}
.f-col{position:absolute}
.f-col h4{font-family:"Roboto Condensed",sans-serif;font-weight:400;font-size:23px;color:var(--blue);margin-bottom:14px}
.f-col li{list-style:none;font-size:15px;color:var(--blue);line-height:31px}
.f-tag{font-size:15px;color:var(--blue);line-height:27px}
.news-item{font-size:15px;color:var(--blue);line-height:23px;margin-bottom:10px}
.news-item small{font-size:14px;display:flex;align-items:center;gap:8px}
.f-contact{font-size:15px;color:var(--blue);display:flex;align-items:center;gap:10px;line-height:34px}
.f-social{display:flex;gap:20px;margin-top:14px}
.f-social span{width:52px;height:52px;border-radius:50%;background:var(--blue)}
.f-social span+span{background:#b9b9b9}
.legal{position:absolute;top:2881px;left:0;width:1200px;height:55px;background:var(--blue);color:var(--white);font-size:15px;text-align:center;line-height:55px}
</style>
</head>
<body>

<header class="site-header">
  <div class="brand"><span class="brand-dot"></span><span class="brand-name">Capt. Wade Harlan</span></div>
  <div class="top-mail">
    <svg width="18" height="13" viewBox="0 0 18 13"><rect x="0.5" y="0.5" width="17" height="12" fill="#0355a3"/><path d="M1 1 L9 7 L17 1" fill="none" stroke="#fff" stroke-width="1.4"/></svg>
    captwade@harlanmail.net
  </div>
  <div class="top-phone">
    <svg width="16" height="16" viewBox="0 0 24 24"><path d="M6.6 10.8c1.4 2.8 3.8 5.1 6.6 6.6l2.2-2.2c.3-.3.7-.4 1-.2 1.1.4 2.3.6 3.6.6.6 0 1 .4 1 1V20c0 .6-.4 1-1 1C10.6 21 3 13.4 3 4c0-.6.4-1 1-1h3.5c.6 0 1 .4 1 1 0 1.3.2 2.5.6 3.6.1.3 0 .7-.2 1z" fill="#fff"/></svg>
    813-555-0172
  </div>
  <div class="top-social" aria-label="Social links"><span></span><span></span><span></span></div>
  <nav class="main-nav">
    <a class="active" href="#">HOME</a><a href="#">ABOUT US</a><a href="#">PICK UP LOCATIONS</a><a href="#">RATES</a><a href="#">CONTACT US</a><a href="#">GIFT CARD</a>
  </nav>
</header>

<section class="hero" role="img" aria-label="Photo of anglers on a boat holding a large tarpon over green water">
  <div class="hero-title">
    <h1>CAPT. WADE HARLAN</h1>
    <p>Come fish with Tampa Bay, FL fishing guide,<br>Tampa Bay fishing charter.</p>
  </div>
  <div class="btn-yellow">CONTACT US NOW</div>
</section>

<section class="welcome">
  <form class="contact-card">
    <h3>CONTACT US</h3>
    <div class="inner">
      <div class="field">Name</div>
      <div class="field">Phone</div>
      <div class="field">Email</div>
      <div class="field tall">Message</div>
      <div class="btn-blue">SUBMIT</div>
    </div>
  </form>
  <h2>WELCOME TO <em>CAPT. WADE HARLAN</em></h2>
  <p>Capt. Wade was born and raised in the Tampa Bay area and fell in love with fishing as a very young boy. He has guided some of the world's top name celebrities and politicians. Through his passion and hard work he has earned a living as a full time guide in the Tampa Bay area for over 25 years. Capt. Wade invites you and your guests to come aboard and enjoy the thrills of fishing for the top gamefish that Tampa Bay has to offer.</p>
  <div class="btn-solid">READ MORE</div>
</section>

<section class="pickup" role="img" aria-label="Background photo of a fishing net with a yellow tint">
  <h2 class="section-title" style="top:48px">PICK UP <em>LOCATIONS</em></h2>
  <p class="sub" style="top:110px">Four Convenient Locations on Every Corner of Tampa Bay</p>
  <p class="sub" style="top:135px">No matter where you might be staying in the Tampa Bay area, Capt. Wade can pick you up nearby.</p>
  <div class="loc" style="left:78px"><div class="map" role="img" aria-label="Map of Heron Cove Marina"></div><div class="label">HERON COVE MARINA</div></div>
  <div class="loc" style="left:438px"><div class="map" role="img" aria-label="Map of Saltmarsh Harbor"></div><div class="label">SALTMARSH HARBOR - BAYWOOD</div></div>
  <div class="loc" style="left:798px"><div class="map" role="img" aria-label="Map of Pelican Point Ramp"></div><div class="label">PELICAN POINT RAMP</div></div>
  <div class="btn-solid view-all" style="top:484px">VIEW ALL
    <svg width="18" height="16" viewBox="0 0 18 16"><path d="M2 2l6 6-6 6M9 2l6 6-6 6" fill="none" stroke="#fff" stroke-width="2.5"/></svg></div>
</section>

<section class="rates">
  <h2 class="section-title" style="top:1802px;color:var(--blue)">RATES</h2>
  <div class="rate-img abs" style="left:78px;top:1886px" role="img" aria-label="Photo of an angler landing a fish at the boat"></div>
  <div class="rate-text" style="left:325px;top:1882px">
    <div class="name">Half Day : 1-2 People</div>
    <div class="price">4 hr &nbsp;| &nbsp;$399.00</div>
    Enjoy a half day charter on Tampa Bay with Capt. Wade.<br><a href="#">BOOK NOW</a>
  </div>
  <div class="rate-img b abs" style="left:616px;top:1886px" role="img" aria-label="Photo of two anglers holding a large fish"></div>
  <div class="rate-text" style="left:863px;top:1882px">
    <div class="name">Half Day : 4 People</div>
    <div class="price">4 hr &nbsp;| &nbsp;$499.00</div>
    Enjoy a half day charter on Tampa Bay with Capt. Wade.<br><a href="#">BOOK NOW</a>
  </div>
  <div class="btn-solid view-all" style="top:2055px;height:52px">VIEW ALL
    <svg width="18" height="16" viewBox="0 0 18 16"><path d="M2 2l6 6-6 6M9 2l6 6-6 6" fill="none" stroke="#fff" stroke-width="2.5"/></svg></div>
</section>

<section class="gift">
  <div class="gift-photo" role="img" aria-label="Photo of the captain in a cap and sunglasses on the water"></div>
  <h2 class="section-title" style="top:2220px;left:78px;width:636px;color:var(--blue)">GIFT CARD</h2>
  <p class="gift-sub" style="top:2280px">Give the Perfect Gift - The Gift of Memories!</p>
  <div class="gift-field" style="left:78px;top:2350px;width:300px;height:40px">Enter Email</div>
  <div class="gift-field" style="left:399px;top:2350px;width:312px;height:40px">Enter Contact No.</div>
  <div class="gift-field" style="left:78px;top:2413px;width:300px;height:40px">From</div>
  <div class="gift-field" style="left:399px;top:2413px;width:312px;height:40px">To</div>
  <div class="gift-field" style="left:78px;top:2475px;width:300px;height:112px;align-items:flex-start;padding-top:10px">Message</div>
  <div class="gift-field" style="left:399px;top:2475px;width:124px;height:40px">Gift Amount</div>
  <div class="gift-note">GIFT BETWEEN 100 USD &amp; 700 USD</div>
  <div class="btn-solid gift-submit">SUBMIT</div>
</section>

<footer class="site-footer">
  <div class="f-col" style="left:78px;top:30px">
    <div style="display:flex;align-items:center;gap:12px;margin-bottom:24px"><span class="brand-dot"></span><span class="brand-name" style="font-size:30px">Capt. Wade Harlan</span></div>
    <div class="f-tag">TAMPA BAY, FISHING GUIDE,<br>TAMPA BAY FISHING CHARTERS</div>
    <div class="f-tag" style="margin-top:4px">Come fish with Tampa Bay.</div>
  </div>
  <div class="f-col" style="left:348px;top:30px">
    <h4>Pickup Locations</h4>
    <ul><li>Heron Cove Marina - St. Petersburg</li><li>Saltmarsh Harbor - Baywood</li><li>Pelican Point Ramp</li><li>Kingfisher Landing Ramp</li></ul>
  </div>
  <div class="f-col" style="left:616px;top:30px">
    <h4>Latest News</h4>
    <div class="news-item">Lorem Ipsum is simply dummy.<small><svg width="14" height="14" viewBox="0 0 14 14"><rect x="1" y="2" width="12" height="11" fill="none" stroke="#0355a3" stroke-width="1.5"/><rect x="1" y="2" width="12" height="3" fill="#0355a3"/></svg>30 September 2016</small></div>
    <div class="news-item">Lorem Ipsum is simply dummy.<small><svg width="14" height="14" viewBox="0 0 14 14"><rect x="1" y="2" width="12" height="11" fill="none" stroke="#0355a3" stroke-width="1.5"/><rect x="1" y="2" width="12" height="3" fill="#0355a3"/></svg>30 September 2016</small></div>
  </div>
  <div class="f-col" style="left:890px;top:30px">
    <h4>Contact Information</h4>
    <div class="f-contact"><svg width="16" height="16" viewBox="0 0 24 24"><path d="M6.6 10.8c1.4 2.8 3.8 5.1 6.6 6.6l2.2-2.2c.3-.3.7-.4 1-.2 1.1.4 2.3.6 3.6.6.6 0 1 .4 1 1V20c0 .6-.4 1-1 1C10.6 21 3 13.4 3 4c0-.6.4-1 1-1h3.5c.6 0 1 .4 1 1 0 1.3.2 2.5.6 3.6.1.3 0 .7-.2 1z" fill="#0355a3"/></svg>813-555-0172</div>
    <div class="f-contact"><svg width="18" height="13" viewBox="0 0 18 13"><rect x="0.75" y="0.75" width="16.5" height="11.5" fill="none" stroke="#0355a3" stroke-width="1.5"/><path d="M1 1 L9 7 L17 1" fill="none" stroke="#0355a3" stroke-width="1.5"/></svg>captwade@harlanmail.net</div>
    <div class="f-social" aria-label="Social links"><span></span><span></span><span></span></div>
  </div>
</footer>
<div class="legal">© <strong>Capt. Wade Harlan</strong> - 2016. &nbsp;All Rights Reserved.</div>

</body>
</html>
```